Business Card Design

New business card design

Target Market(s)

Residential & Commercial Property Managers

Industry/Entity Type

Plumbing Services

Contact Information for Business Card

Name - Rowan Keddle, title - Director, Phone Number - 0431 286 517, email - rowan@tbk-plumbing.com.au, Company ABN - 73 215 904 386,

Font styles to use
Sans Serif

Colors
0054AA
0677BA
7BADD7
CADEEF
E8F1F8

```html
<!DOCTYPE html>
<html lang="en">
<head>
<meta charset="utf-8">
<title>TBK Plumbing Services – Business Card</title>
<link rel="stylesheet" href="https://fonts.googleapis.com/css2?family=Questrial&family=Yanone+Kaffeesatz:wght@400;600&display=swap">
<style>
  :root {
    --backdrop: #c9ced4;
    --backdrop-dark: #9aa2ab;
    --card-white: #ffffff;
    --sky: #0aaee9;
    --sky-deep: #0599d6;
    --sky-light: #3cc3f2;
    --ink: #1f2a33;
    --ink-soft: #6e6e6e;
    --accent: #1aa3e0;
  }
  * { margin: 0; padding: 0; box-sizing: border-box; }
  html, body { width: 1200px; height: 675px; overflow: hidden; }
  body {
    background: radial-gradient(ellipse at 40% 60%, #e4e7ea 0%, var(--backdrop) 55%, var(--backdrop-dark) 100%);
    font-family: "Questrial", sans-serif;
    position: relative;
  }
  .card {
    position: absolute;
    top: 178px;
    width: 520px;
    height: 318px;
    border-radius: 3px;
    overflow: hidden;
    box-shadow: 0 18px 40px rgba(40, 50, 60, 0.28);
  }
  .card--front { left: 50px; }
  .card--back { left: 630px; background: var(--card-white); }

  .droplet-texture {
    position: absolute; inset: 0;
    background: radial-gradient(circle at 30% 30%, var(--sky-light) 0%, var(--sky) 45%, var(--sky-deep) 100%);
  }
  .front-brand {
    position: absolute; inset: 0;
    display: flex; align-items: center; justify-content: center; gap: 14px;
  }
  .brand-dot {
    width: 16px; height: 16px; border-radius: 50%;
    background: var(--card-white);
  }
  .brand-name {
    font-family: "Questrial", sans-serif;
    font-size: 34px;
    letter-spacing: 2px;
    color: var(--card-white);
  }

  .back-brand {
    position: absolute; left: 28px; top: 0; bottom: 0; width: 290px;
    display: flex; align-items: center; gap: 10px;
  }
  .back-brand .brand-name { color: var(--ink); font-size: 25px; letter-spacing: 1px; }
  .back-brand .brand-dot { background: var(--accent); width: 12px; height: 12px; }

  .divider {
    position: absolute; left: 318px; top: 72px;
    width: 1px; height: 160px; background: var(--ink);
  }
  .contact {
    position: absolute; left: 334px; top: 70px;
    font-family: "Yanone Kaffeesatz", sans-serif;
    color: var(--ink-soft);
    list-style: none;
  }
  .contact__name { font-weight: 600; font-size: 27px; color: var(--accent); line-height: 1; letter-spacing: 0.5px; }
  .contact__title { font-size: 16px; margin: 2px 0 8px; }
  .contact__line { display: flex; align-items: center; gap: 6px; font-size: 16px; line-height: 1.35; letter-spacing: 0.6px; }
  .contact__line svg { width: 11px; height: 11px; fill: var(--accent); flex: none; }
  .contact__abn { font-size: 18px; margin-top: 8px; letter-spacing: 0.5px; }
  .contact__abn span { color: var(--accent); }
</style>
</head>
<body>
  <section class="card card--front" aria-label="Business card front">
    <div class="droplet-texture" role="img" aria-label="Blue background covered in water droplets"></div>
    <div class="front-brand">
      <span class="brand-dot"></span>
      <span class="brand-name">TBK Plumbing Services</span>
    </div>
  </section>

  <section class="card card--back" aria-label="Business card back">
    <div class="back-brand">
      <span class="brand-dot"></span>
      <span class="brand-name">TBK Plumbing Services</span>
    </div>
    <div class="divider"></div>
    <ul class="contact">
      <li class="contact__name">Rowan Keddle</li>
      <li class="contact__title">Director</li>
      <li class="contact__line">
        <svg viewBox="0 0 24 24"><path d="M6.6 10.8a15.1 15.1 0 0 0 6.6 6.6l2.2-2.2a1 1 0 0 1 1-.25 11.4 11.4 0 0 0 3.6.57 1 1 0 0 1 1 1V20a1 1 0 0 1-1 1A17 17 0 0 1 3 4a1 1 0 0 1 1-1h3.5a1 1 0 0 1 1 1c0 1.25.2 2.45.57 3.57a1 1 0 0 1-.25 1z"/></svg>
        0431 286 517
      </li>
      <li class="contact__line">
        <svg viewBox="0 0 24 24"><path d="M2 5h20v14H2z M2 5l10 8 10-8" stroke="#fff" stroke-width="1.5"/></svg>
        rowan@tbk-plumbing.com.au
      </li>
      <li class="contact__line">
        <svg viewBox="0 0 24 24"><circle cx="12" cy="12" r="10"/><path d="M2 12h20M12 2c3 3 3 17 0 20M12 2c-3 3-3 17 0 20" stroke="#fff" stroke-width="1.4" fill="none"/></svg>
        tbk-plumbing.com.au
      </li>
      <li class="contact__abn"><span>ABN</span> - 73 215 904 386</li>
    </ul>
  </section>
</body>
</html>
```